real esate business card with company logo and name

we need a business card design for a real esate company

The company name is Walsh & Brand Pty Ltd, and we have our logo designed and will upload. We want classic or moden feel. Black or white background. looks more textured. Should include folowinginformations
Owen Walsh and Lucy Brand
Sales Agents & Onsite Manager
p: 07 5948 2063
F: 07 5948 2174
M:0431 857 219
3/42 Marlow Crescent, FERNLEA QLD 4213

We want this business card looks professonal. Thank you in advance.

Industry/Entity Type

Real Estate Agent

Contact Information for Business Card

Owen Walsh and Lucy Brand
Onsite Manager & Sales Agents
p: 07 5948 2063
M:0431 857 219

Font styles to use
Serif

Colors
000000
fbfbfb
333333
959595

Requirements
Must have
• company logo and name, black or white back ground

```html
<!DOCTYPE html>
<html lang="en">
<head>
<meta charset="utf-8">
<title>Walsh &amp; Brand Pty Ltd — Business Card</title>
<link rel="stylesheet" href="https://fonts.googleapis.com/css2?family=Open+Sans:wght@400;600;700&display=swap">
<style>
  :root {
    --ink: #000000;
    --paper: #fbfbfb;
    --charcoal: #333333;
    --slate: #58595b;
    --mid-grey: #959595;
    --swoosh: #cfcfcf;
    --backdrop: #e4e4e4;
  }
  * { margin: 0; padding: 0; box-sizing: border-box; }
  html, body {
    width: 1200px; height: 900px; overflow: hidden;
    background: var(--backdrop);
    font-family: "Open Sans", Arial, sans-serif;
  }
  .canvas {
    position: relative; width: 1200px; height: 900px;
  }
  .card {
    position: absolute; left: 280px;
    width: 640px; height: 366px;
    overflow: hidden;
    box-shadow: 0 4px 14px rgba(0,0,0,0.18);
  }
  /* Back side */
  .card-back { top: 64px; background: var(--slate); }
  .card-back .brand {
    position: absolute; left: 0; right: 0; top: 0; bottom: 0;
    display: flex; flex-direction: column; align-items: center; justify-content: center; gap: 22px;
  }
  .brand-mark {
    width: 56px; height: 56px; background: var(--paper);
  }
  .brand-name {
    font-weight: 600; letter-spacing: 2px; text-transform: uppercase;
  }
  .card-back .brand-name { color: var(--paper); font-size: 22px; }

  /* Front side */
  .card-front { top: 470px; background: var(--slate); }
  .card-front .shape { position: absolute; inset: 0; }
  .card-front .brand {
    position: absolute; left: 0; top: 0; width: 270px; height: 366px;
    display: flex; flex-direction: column; align-items: center; justify-content: center; gap: 20px;
    padding-right: 20px;
  }
  .card-front .brand-mark { width: 60px; height: 60px; background: var(--mid-grey); }
  .card-front .brand-name { color: var(--mid-grey); font-size: 17px; letter-spacing: 1.5px; }

  .details {
    position: absolute; right: 34px; top: 46px;
    width: 300px; text-align: right; color: var(--paper);
  }
  .agent-names { font-size: 19px; font-weight: 700; line-height: 1.2; }
  .agent-role { font-size: 15px; margin-top: 3px; }
  .contacts { list-style: none; margin-top: 42px; font-size: 15px; line-height: 1.45; }
  .contacts li { display: flex; justify-content: flex-end; align-items: center; gap: 8px; }
  .contacts svg { width: 14px; height: 14px; fill: var(--paper); }
  .address { font-style: normal; font-size: 15px; line-height: 1.45; margin-top: 28px; padding-right: 22px; }
</style>
</head>
<body>
<main class="canvas">
  <section class="card card-back" aria-label="Business card back">
    <div class="brand">
      <span class="brand-mark"></span>
      <span class="brand-name">Walsh &amp; Brand Pty Ltd.</span>
    </div>
  </section>

  <section class="card card-front" aria-label="Business card front">
    <svg class="shape" viewBox="0 0 640 366" width="640" height="366" aria-hidden="true">
      <path d="M270 0 C338 80 328 262 188 366 H226 C360 262 368 80 296 0 Z" fill="var(--swoosh)"/>
      <path d="M0 0 H270 C330 80 318 262 178 366 H0 Z" fill="var(--ink)"/>
    </svg>
    <div class="brand">
      <span class="brand-mark"></span>
      <span class="brand-name">Walsh &amp; Brand Pty Ltd.</span>
    </div>
    <div class="details">
      <p class="agent-names">Owen Walsh and Lucy Brand</p>
      <p class="agent-role">Onsite Manager &amp; Sales Agents</p>
      <ul class="contacts">
        <li>07 5948 2063
          <svg viewBox="0 0 16 16" aria-label="Phone"><path d="M1 6 C1 3 4 2 8 2 C12 2 15 3 15 6 L11 6 L10.5 4.5 H5.5 L5 6 Z M4 7 H12 L14 13 H2 Z"/></svg>
        </li>
        <li>0431 857 219
          <svg viewBox="0 0 16 16" aria-label="Mobile"><path d="M4 1 H12 V15 H4 Z M5.5 2.5 V11.5 H10.5 V2.5 Z M7.2 12.6 H8.8 V13.8 H7.2 Z" fill-rule="evenodd"/></svg>
        </li>
      </ul>
      <address class="address">3/42 Marlow Crescent,<br>FERNLEA QLD 4213</address>
    </div>
  </section>
</main>
</body>
</html>
```